Tolvik Commercial Cleaning is lookong for a new business card design.

A fresh new design that's professional and stylish. We need a serious upgrade to our business cards. I have included pictures of our existing ones. Our clients include professional individuals and business owners. We woupdblike something professional and upbeat. Please have fun and see what you come uo with.

Target Market(s)

Property managers, business owners, facility managers and other similar professionals

Industry/Entity Type

Janitorial

Contact Information for Business Card

Name, cell, office number, email, web address

Font styles to use
Sans Serif

Colors

Designer to choose colors to be used in the design.

Requirements
Must have
• please use the green color in our logo
Nice to have
• Bar code
Should not have
• Address

```html
<!DOCTYPE html>
<html lang="en">
<head>
<meta charset="utf-8">
<title>Tolvik Commercial Cleaning – Business Card</title>
<link rel="stylesheet" href="https://fonts.googleapis.com/css2?family=Open+Sans:wght@400;600;700&display=swap">
<style>
  :root {
    --stage: #2b2b30;
    --card: #1f1f24;
    --green: #3ab85a;
    --blue: #3f78ba;
    --white: #ffffff;
    --edge: 2px;
  }
  * { box-sizing: border-box; margin: 0; padding: 0; }
  html, body {
    width: 1200px;
    height: 780px;
    overflow: hidden;
    background: var(--stage);
    font-family: "Open Sans", Arial, sans-serif;
  }
  .stage {
    position: relative;
    width: 1200px;
    height: 780px;
  }
  .card {
    position: absolute;
    top: 40px;
    width: 400px;
    height: 700px;
    background: var(--card);
    border: var(--edge) solid var(--green);
    overflow: hidden;
  }
  .card--front {
    left: 170px;
    border-radius: 170px 0 170px 0;
  }
  .card--back {
    left: 630px;
    border-radius: 0 170px 0 170px;
  }

  /* front */
  .front-brand {
    position: absolute;
    left: 50%;
    top: 50%;
    width: 560px;
    transform: translate(-50%, -50%) rotate(90deg);
    text-align: center;
    color: var(--green);
    font-weight: 700;
    font-size: 54px;
    line-height: 1.12;
    letter-spacing: 0.5px;
  }

  /* back */
  .back-brand {
    position: absolute;
    top: 92px;
    left: 0;
    right: 0;
    text-align: center;
    color: var(--green);
    font-weight: 700;
    font-size: 32px;
    line-height: 1.15;
  }
  .contact-block {
    position: absolute;
    left: 0;
    right: 0;
    top: 420px;
    text-align: center;
  }
  .person-name {
    font-weight: 700;
    font-size: 30px;
    line-height: 1.1;
  }
  .person-name__first { color: var(--green); }
  .person-name__last { color: var(--blue); }
  .person-role {
    color: var(--white);
    font-size: 16px;
    font-weight: 600;
    margin-top: 4px;
  }
  .contact-icons {
    display: flex;
    justify-content: center;
    gap: 10px;
    margin-top: 18px;
  }
  .contact-icon {
    width: 30px;
    height: 30px;
    border-radius: 50%;
    background: var(--green);
    display: flex;
    align-items: center;
    justify-content: center;
  }
  .contact-list {
    list-style: none;
    margin-top: 16px;
    color: var(--white);
    font-size: 17px;
    line-height: 1.5;
  }
</style>
</head>
<body>
<main class="stage">
  <section class="card card--front" aria-label="Card front">
    <p class="front-brand">Tolvik<br>Commercial<br>Cleaning</p>
  </section>

  <section class="card card--back" aria-label="Card back">
    <p class="back-brand">Tolvik<br>Commercial Cleaning</p>

    <div class="contact-block">
      <h1 class="person-name">
        <span class="person-name__first">Mara</span>
        <span class="person-name__last">Ellison</span>
      </h1>
      <p class="person-role">Director</p>

      <div class="contact-icons">
        <span class="contact-icon" aria-label="Phone">
          <svg width="16" height="16" viewBox="0 0 24 24" fill="#ffffff" aria-hidden="true">
            <path d="M6.6 10.8a15.2 15.2 0 0 0 6.6 6.6l2.2-2.2c.3-.3.7-.4 1-.2 1.1.4 2.3.6 3.6.6.6 0 1 .4 1 1V20c0 .6-.4 1-1 1A17 17 0 0 1 3 4c0-.6.4-1 1-1h3.5c.6 0 1 .4 1 1 0 1.3.2 2.5.6 3.6.1.3 0 .7-.2 1z"/>
          </svg>
        </span>
        <span class="contact-icon" aria-label="Email">
          <svg width="16" height="16" viewBox="0 0 24 24" fill="none" stroke="#ffffff" stroke-width="2" aria-hidden="true">
            <rect x="3" y="5" width="18" height="14" rx="1.5"/>
            <path d="M3 6l9 7 9-7"/>
          </svg>
        </span>
        <span class="contact-icon" aria-label="Website">
          <svg width="16" height="16" viewBox="0 0 24 24" fill="none" stroke="#ffffff" stroke-width="2" aria-hidden="true">
            <circle cx="12" cy="12" r="9"/>
            <path d="M3 12h18M12 3c3 3.2 3 14.8 0 18M12 3c-3 3.2-3 14.8 0 18"/>
          </svg>
        </span>
      </div>

      <ul class="contact-list">
        <li>(555) 014-2287</li>
        <li>mara@tolvikcleaning.com</li>
        <li>www.tolvikcleaning.com</li>
      </ul>
    </div>
  </section>
</main>
</body>
</html>
```